Business card

I have changed logo's and colors. I have uploaded the new logo and colors.

In my head I am thinking about the main logo and text beside logo to be on one side of the card. The other side of the card to have just my picture and contact information.

The "R" emblem and the "equal housing" emblem... cut he MLS from the "R". and remove the wording from the house emblem.

Info on Card:

Lyle Penrose
Designated Broker, CDPE, CNE, GRI
Direct: 602.555.0143
Fax: 623.555.0187
Lyle@PenroseandAssociates.example
www.PenroseandAssociates.example
4153 West Marlow Lane Glendale, AZ 85391

Please see brief as I have uploaded a new logo and a few notes.

Reason: I changed the logo and colors. Please see brief

I am leaning towards maybe a black business card(or at least on the front where the logo is). I liked several designs that were submitted. Please re-submit.

```html
<!DOCTYPE html>
<html lang="en">
<head>
<meta charset="utf-8">
<title>Penrose &amp; Associates — Business Card</title>
<link rel="stylesheet" href="https://fonts.googleapis.com/css2?family=Cinzel:wght@400;600&family=Open+Sans:wght@400;600&display=swap">
<style>
  :root {
    --backdrop: #1c2a36;
    --card-face: #3b3b3d;
    --card-face-dark: #2f2f31;
    --band-black: #0d0d0e;
    --chrome-light: #f2f2f2;
    --chrome-mid: #9a9a9c;
    --chrome-dark: #4a4a4c;
    --text-silver: #d9d9db;
    --text-muted: #c4c4c6;
    --brass-light: #d8cf7a;
    --brass-mid: #aea24a;
    --brass-dark: #6f6627;
    --brass-ink: #3a3512;
    --strip-dark: #262628;
    --pill: #2a2a2c;
  }
  * { box-sizing: border-box; margin: 0; padding: 0; }
  html, body { width: 1200px; height: 900px; overflow: hidden; }
  body {
    background: var(--backdrop);
    font-family: "Open Sans", Arial, sans-serif;
    position: relative;
  }
  .card {
    position: absolute;
    left: 250px;
    width: 700px;
    height: 400px;
    border-radius: 6px;
    overflow: hidden;
    background: radial-gradient(ellipse at 50% 40%, var(--card-face) 0%, var(--card-face-dark) 100%);
    box-shadow: 0 14px 30px rgba(0,0,0,.45);
  }
  .card--front { top: 40px; }
  .card--back  { top: 460px; }

  .card__band {
    position: absolute;
    left: 0; right: 0;
    height: 34px;
    background: var(--band-black);
  }
  .card__band--top { top: 0; }
  .card__band--bottom { bottom: 0; }
  .card__chrome {
    position: absolute;
    left: 0; right: 0;
    height: 6px;
    background: linear-gradient(90deg, var(--chrome-dark), var(--chrome-light) 30%, var(--chrome-mid) 60%, var(--chrome-light) 85%, var(--chrome-dark));
  }
  .card__chrome--top { top: 34px; }
  .card__chrome--bottom { bottom: 34px; }

  /* front */
  .brand {
    position: absolute;
    left: 110px; top: 78px;
    display: flex; align-items: center; gap: 26px;
  }
  .brand__disc {
    width: 112px; height: 112px; border-radius: 50%;
    background: linear-gradient(160deg, #b9bcc0, #6d7075);
  }
  .brand__name {
    font-family: "Cinzel", Georgia, serif;
    font-weight: 600;
    font-size: 38px;
    line-height: 1.1;
    color: var(--text-silver);
    letter-spacing: 1px;
  }
  .contact {
    position: absolute;
    color: var(--text-muted);
    font-size: 17px;
    white-space: nowrap;
  }
  .contact--direct { left: 150px; top: 240px; }
  .contact--fax { right: 130px; top: 225px; font-size: 15px; }
  .contact--address { left: 0; right: 0; top: 300px; text-align: center; padding-left: 120px; }

  /* back */
  .strip {
    position: absolute;
    left: 0; right: 0; top: 150px; height: 30px;
    background: var(--strip-dark);
    border-top: 1px solid #1a1a1b;
    border-bottom: 1px solid #4a4a4c;
  }
  .plate {
    position: absolute;
    left: 155px; top: 68px;
    width: 390px; height: 165px;
    border: 5px solid var(--brass-dark);
    outline: 2px solid var(--brass-light);
    outline-offset: -9px;
    background: linear-gradient(150deg, var(--brass-light), var(--brass-mid) 55%, var(--brass-dark));
    box-shadow: 0 6px 14px rgba(0,0,0,.5);
    display: flex; flex-direction: column; justify-content: center; align-items: center;
    font-family: "Cinzel", Georgia, serif;
  }
  .plate__rivet {
    position: absolute; width: 9px; height: 9px; border-radius: 50%;
    background: var(--brass-dark);
  }
  .plate__rivet--tl { top: 4px; left: 4px; }
  .plate__rivet--tr { top: 4px; right: 4px; }
  .plate__rivet--bl { bottom: 4px; left: 4px; }
  .plate__rivet--br { bottom: 4px; right: 4px; }
  .plate__name {
    font-size: 40px; font-weight: 400; color: #eee9b4; letter-spacing: 1px;
  }
  .plate__title {
    margin-top: 6px;
    font-size: 24px; font-weight: 600; color: var(--brass-ink);
    border-bottom: 2px solid var(--brass-ink);
    white-space: nowrap;
  }
  .plate__credentials { font-size: 11px; font-family: "Open Sans", Arial, sans-serif; margin-left: 6px; }
  .web-pill {
    position: absolute;
    left: 36px; right: 36px; top: 300px; height: 36px;
    border-radius: 18px;
    background: var(--pill);
    box-shadow: inset 0 2px 4px rgba(0,0,0,.6);
    display: flex; align-items: center; justify-content: space-between;
    gap: 40px;
    padding: 0 22px;
    color: var(--text-silver);
    font-size: 15px;
    white-space: nowrap;
  }
</style>
</head>
<body>

  <section class="card card--front" aria-label="Card front">
    <div class="card__band card__band--top"></div>
    <div class="card__chrome card__chrome--top"></div>
    <div class="brand">
      <div class="brand__disc"></div>
      <div class="brand__name">Penrose<br>&amp; Associates</div>
    </div>
    <p class="contact contact--fax">Fax: 623.555.0187</p>
    <p class="contact contact--direct">Direct: 602.555.0143</p>
    <p class="contact contact--address">4153 West Marlow Lane Glendale, AZ 85391</p>
    <div class="card__chrome card__chrome--bottom"></div>
    <div class="card__band card__band--bottom"></div>
  </section>

  <section class="card card--back" aria-label="Card back">
    <div class="card__band card__band--top"></div>
    <div class="card__chrome card__chrome--top"></div>
    <div class="strip"></div>
    <div class="plate">
      <span class="plate__rivet plate__rivet--tl"></span>
      <span class="plate__rivet plate__rivet--tr"></span>
      <span class="plate__rivet plate__rivet--bl"></span>
      <span class="plate__rivet plate__rivet--br"></span>
      <p class="plate__name">LYLE PENROSE</p>
      <p class="plate__title">Designated Broker<span class="plate__credentials">CDPE, CNE, GRI</span></p>
    </div>
    <div class="web-pill">
      <span class="web-pill__email">Lyle@PenroseandAssociates.example</span>
      <span class="web-pill__site">www.PenroseandAssociates.example</span>
    </div>
    <div class="card__chrome card__chrome--bottom"></div>
    <div class="card__band card__band--bottom"></div>
  </section>

</body>
</html>
```